Artsy 1 Page Website/Brochure for climate change investment company

We want art like feel similar to https://velmora.quintrel.net/ for a 1 page online website (1 page) to have an online presence. We want to show credibility, no functionality. The only call to action is an email to the company.
3 sections 1) Company 2) Services, 3) brands.
The idea is 1) we are credible and serious, 2) market is increasing, 3) knowledge about sector, 4) large branded companies in the sector.
We want users to be interested and want to learn more.
There should be 1 or 2 animated sections. 1) GHG (green house gases) floating up or something showing emissions rising, 2) Services can scroll or loop.
See my mockup. The font should be standardized. The text shapes should be same. Keep same color palette unless you have better idea.
https://slides.brovanta.com/deck/7KxQ2mPzT9wLbV4nRfYcHd8sJuA6eGtNqXoZ1iMvBkE/view?ref=share
Logo for company AirLedgerHub.com

Target Market(s)

Potential Investors and Academics and Industry specialist. This is not for general consumers

Industry/Entity Type

Environment/Investors

Number of Pages Required

1 page

Requirements
Must have
• Artsy feel like a brochure
Should not have
• I do not want a functional website with lots of standard menus e.g. menus at the top

```html
<!DOCTYPE html>
<html lang="en">
<head>
<meta charset="utf-8">
<title>AirLedgerHub</title>
<link rel="stylesheet" href="https://fonts.googleapis.com/css2?family=Exo+2:wght@800;900&family=Roboto:wght@500;700&display=swap">
<style>
  :root{
    --page:#8f8f8f;
    --magenta:#c4004f;
    --navy:#14104e;
    --olive:#7a7468;
    --olive-light:#857e71;
    --disc:#404040;
    --disc-num:#5c5c5c;
    --night:#070707;
    --ring:#1c1c1c;
    --green:#7d9b3c;
    --white:#ffffff;
  }
  *{box-sizing:border-box;margin:0;padding:0}
  html,body{width:752px;height:1200px;overflow:hidden}
  body{background:var(--page);position:relative;font-family:"Roboto",Arial,sans-serif;color:var(--white)}
  .panel{position:absolute;left:58px;width:636px;height:353px;overflow:hidden;box-shadow:0 18px 40px rgba(0,0,0,.45)}
  .display{font-family:"Exo 2",Arial,sans-serif;font-weight:900;position:absolute;line-height:1;white-space:nowrap}

  /* company */
  .company{top:45px;background:var(--magenta)}
  .company .ripple-photo{position:absolute;left:60px;top:140px;width:600px;height:240px;
    background:radial-gradient(ellipse 50% 45% at 50% 60%, rgba(20,16,78,.85), rgba(20,16,78,.35) 60%, rgba(196,0,79,0) 100%)}
  .brand-name{left:44px;top:50px;font-size:30px;letter-spacing:.3px;font-weight:800}
  .connect{position:absolute;left:341px;top:51px}
  .connect .label{font-size:11px;font-weight:500;letter-spacing:.2px}
  .connect .mail{display:flex;align-items:center;gap:7px;margin-top:8px;font-size:17px;font-weight:500}

  .gas{position:absolute;left:27px;width:30px;height:61px;border:1.5px solid var(--white);border-radius:15px}
  .gas svg{position:absolute;left:0;top:0}
  .gas.is-active{border:none}
  .company .gas.is-active{background:var(--green)}
  .services .gas.is-active{background:var(--magenta)}

  /* services */
  .services{top:423px;background:var(--olive)}
  .services .water-photo{position:absolute;left:120px;top:150px;width:520px;height:220px;
    background:radial-gradient(ellipse 50% 42% at 55% 50%, var(--olive-light), rgba(122,116,104,0) 70%)}
  .services-ghost{left:160px;top:8px;font-size:100px;color:rgba(255,255,255,.06);letter-spacing:-1px}
  .services-title{left:25px;top:31px;font-size:40px}
  .service{position:absolute;width:106px;height:106px;border-radius:50%;background:var(--disc);text-align:center}
  .service .num{font-weight:700;font-size:29px;color:var(--disc-num);margin-top:16px;line-height:1}
  .service .name{font-size:8.5px;font-weight:500;line-height:11.5px;margin-top:6px}
  .service.is-featured{background:none}
  .service.is-featured svg{position:absolute;left:0;top:0}
  .service.is-featured .name{position:absolute;left:0;right:0;top:27px;margin-top:0;font-size:10px;line-height:13px;color:var(--disc)}

  /* partners */
  .space{top:801px;background:var(--night)}
  .space-ghost{left:48px;top:12px;font-size:100px;color:rgba(255,255,255,.05);letter-spacing:-1px}
  .space-title{left:25px;top:24px;font-size:40px}
  .partner{position:absolute;width:96px;height:96px;border-radius:50%;border:6px solid var(--ring);display:flex;align-items:center;justify-content:center;text-align:center;font-size:10px;font-weight:700;color:#d9d9d9;line-height:12px;padding:0 6px}
  .partner.is-selected{border-color:var(--magenta)}
  .partner .cursor{position:absolute;left:44px;top:56px}
</style>
</head>
<body>

<section class="panel company">
  <div class="ripple-photo" role="img" aria-label="Photograph of a water ripple, tinted navy on magenta"></div>
  <h1 class="display brand-name">AIRLEDGERHUB</h1>
  <div class="connect">
    <p class="label">CONNECT</p>
    <p class="mail">
      <svg width="17" height="13" viewBox="0 0 17 13"><rect x="0" y="0" width="17" height="13" rx="1.5" fill="#fff"/><path d="M0.5 1 L8.5 7.5 L16.5 1" fill="none" stroke="#c4004f" stroke-width="1.6"/></svg>
      partners@airledgerhub.com
    </p>
  </div>
  <div class="gas" style="top:115px"><svg width="30" height="61"><path d="M15 22V9M10 14l5-5 5 5" stroke="#fff" stroke-width="2" fill="none"/><text transform="translate(21 54) rotate(-90)" fill="#fff" font-family="Roboto" font-weight="700" font-size="13">CH<tspan font-size="8" dy="3">4</tspan></text></svg></div>
  <div class="gas" style="top:188px"><svg width="30" height="61"><path d="M15 22V9M10 14l5-5 5 5" stroke="#fff" stroke-width="2" fill="none"/><text transform="translate(21 55) rotate(-90)" fill="#fff" font-family="Roboto" font-weight="700" font-size="13">GHG</text></svg></div>
  <div class="gas is-active" style="top:261px"><svg width="30" height="61"><path d="M15 22V9M10 14l5-5 5 5" stroke="#fff" stroke-width="2" fill="none"/><text transform="translate(21 55) rotate(-90)" fill="#fff" font-family="Roboto" font-weight="700" font-size="13">CO<tspan font-size="8" dy="3">2</tspan></text></svg></div>
</section>

<section class="panel services">
  <div class="water-photo" role="img" aria-label="Photograph of a soft ripple in muted olive water"></div>
  <p class="display services-ghost" aria-hidden="true">SERVICES</p>
  <h2 class="display services-title">SERVICES</h2>
  <div class="gas" style="top:115px"><svg width="30" height="61"><path d="M15 22V9M10 14l5-5 5 5" stroke="#fff" stroke-width="2" fill="none"/><text transform="translate(21 54) rotate(-90)" fill="#fff" font-family="Roboto" font-weight="700" font-size="13">CH<tspan font-size="8" dy="3">4</tspan></text></svg></div>
  <div class="gas" style="top:188px"><svg width="30" height="61"><path d="M15 22V9M10 14l5-5 5 5" stroke="#fff" stroke-width="2" fill="none"/><text transform="translate(21 55) rotate(-90)" fill="#fff" font-family="Roboto" font-weight="700" font-size="13">GHG</text></svg></div>
  <div class="gas is-active" style="top:261px"><svg width="30" height="61"><path d="M15 22V9M10 14l5-5 5 5" stroke="#fff" stroke-width="2" fill="none"/><text transform="translate(21 55) rotate(-90)" fill="#fff" font-family="Roboto" font-weight="700" font-size="13">CO<tspan font-size="8" dy="3">2</tspan></text></svg></div>

  <div class="service" style="left:129px;top:97px"><p class="num">01</p><p class="name">CARBON<br>CAPTURE</p></div>
  <div class="service is-featured" style="left:239px;top:97px">
    <svg width="106" height="106" viewBox="0 0 106 106">
      <circle cx="53" cy="53" r="53" fill="#2a2a2a"/>
      <circle cx="53" cy="53" r="46" fill="#fff"/>
      <text x="53" y="34" text-anchor="middle" font-family="Roboto" font-weight="700" font-size="27" fill="#e6e6e6">02</text>
      <g stroke="#2a2a2a" stroke-width="2.4">
        <line x1="8" y1="62" x2="98" y2="62"/><line x1="9" y1="67" x2="97" y2="67"/>
        <line x1="11" y1="72" x2="95" y2="72"/><line x1="14" y1="78" x2="92" y2="78"/>
        <line x1="19" y1="84" x2="87" y2="84"/><line x1="26" y1="90" x2="80" y2="90"/>
      </g>
    </svg>
    <p class="name">NATURE BASED<br>SOLUTIONS</p>
  </div>
  <div class="service" style="left:349px;top:97px"><p class="num">03</p><p class="name">TECHNOLOGY<br>BASED<br>SOLUTIONS</p></div>
  <div class="service" style="left:459px;top:97px"><p class="num">04</p><p class="name">PERMANENT<br>CARBON<br>REMOVAL</p></div>

  <div class="service" style="left:130px;top:216px"><p class="num" style="margin-top:20px">05</p><p class="name">NEW<br>METHODOLOGIES</p></div>
  <div class="service" style="left:243px;top:216px"><p class="num" style="margin-top:20px">06</p><p class="name">REDD+</p></div>
  <div class="service" style="left:356px;top:216px"><p class="num" style="margin-top:20px">07</p><p class="name">STREAMING</p></div>
  <div class="service" style="left:470px;top:216px"><p class="num" style="margin-top:20px">08</p><p class="name">CARBON MARKETS</p></div>
</section>

<section class="panel space">
  <p class="display space-ghost" aria-hidden="true">OUR SPACE</p>
  <h2 class="display space-title">OUR SPACE</h2>

  <div class="partner" style="left:27px;top:91px">Norvel</div>
  <div class="partner is-selected" style="left:128px;top:91px">Tarvik
    <svg class="cursor" width="12" height="16" viewBox="0 0 12 16"><path d="M1 1v12l3-3 2.5 5 2-1-2.5-5H10z" fill="#fff" stroke="#000" stroke-width="1"/></svg>
  </div>
  <div class="partner" style="left:230px;top:91px">Emission Accord</div>
  <div class="partner" style="left:332px;top:91px">Cartwell</div>
  <div class="partner" style="left:433px;top:91px">Payrune</div>
  <div class="partner" style="left:535px;top:91px">Lumora</div>

  <div class="partner" style="left:27px;top:201px">Continental Council</div>
  <div class="partner" style="left:128px;top:201px">Kestor</div>
  <div class="partner" style="left:230px;top:201px">Auric Mark</div>
  <div class="partner" style="left:332px;top:201px">Climora</div>
  <div class="partner" style="left:433px;top:201px">Regional Pact</div>
  <div class="partner" style="left:535px;top:201px">Terra Summit 2021</div>
</section>

</body>
</html>
```